Norrell Advisory WA Business Card

Create an interesting, eye catching and colourful two sided business card. We are a business consulting operation assisting SME's improve all areas of their business. We provide consulting services to assist SME's to create a culture of continuous improvement, making a positive difference in the business. Our tag line is Small changes, big rewards. We want to create a well recognised, innovative brand that can be continued throughout our website, social media and email correspondence.

Target Market(s)

Small to Medium Enterprise Business Owners

Industry/Entity Type

Business Consultant

Contact Information for Business Card

Name of Business: Norrell Advisory - Steady steps lasting gains
Derek Holloway Ph 0407385510 Megan Holloway Ph 0407913847
Email norrelladvisorywa@mailbox-example.com
Web address TBA
FaceBook page TBA

BACKSIDE OF CARD

Providing assistance with:

• Organisation & Efficiency
• Revenue generation & Marketing
• Financial Management
• Production quality & delivery
• Systems & Process documentation
• Exit Strategy

Font styles to use
Other font styles liked:
• Calibri

Colors

Designer to choose colors to be used in the design.

Requirements
Must have
• Calibri font

```html
<!DOCTYPE html>
<html lang="en">
<head>
<meta charset="utf-8">
<title>Norrell Advisory WA – Business Card</title>
<link rel="stylesheet" href="https://fonts.googleapis.com/css2?family=Carlito:wght@400;700&family=Open+Sans:wght@400;700&display=swap">
<style>
  :root {
    --page-bg: #e4e4e4;
    --card-bg: #ffffff;
    --band: #2e2d2c;
    --ink: #2f2f2f;
    --ink-soft: #555555;
    --blue: #0f78b4;
    --yellow: #f7c42a;
    --white: #ffffff;
  }
  * { box-sizing: border-box; margin: 0; padding: 0; }
  html, body {
    width: 1125px; height: 1200px; overflow: hidden;
    background: var(--page-bg);
  }
  .canvas { position: relative; width: 1125px; height: 1200px; }
  .card {
    position: absolute; left: 171px; width: 826px; height: 472px;
    background: var(--card-bg); border-radius: 24px; overflow: hidden;
  }
  .card--front { top: 106px; }
  .card--back { top: 639px; }

  /* Front */
  .front-title {
    position: absolute; top: 62px; left: 0; width: 100%; text-align: center;
    font-family: "Open Sans", sans-serif; font-weight: 700; font-size: 37px;
    color: var(--ink); letter-spacing: 0.3px;
  }
  .band {
    position: absolute; top: 175px; left: 0; width: 100%; height: 161px;
    background: var(--band);
  }
  .person { position: absolute; left: 60px; top: 54px; font-family: "Carlito", sans-serif; }
  .person-name { font-weight: 700; font-size: 31px; color: var(--blue); line-height: 1; }
  .person-phone { font-weight: 700; font-size: 19px; color: var(--yellow); margin-top: 6px; }
  .brand-mark {
    position: absolute; left: 320px; top: 0; width: 130px; height: 161px;
    display: flex; align-items: center; justify-content: center; gap: 8px;
  }
  .brand-mark .dot { width: 14px; height: 14px; background: var(--yellow); flex: none; }
  .brand-mark .brand-name {
    font-family: "Open Sans", sans-serif; font-weight: 700; font-size: 17px;
    color: var(--white); line-height: 1.15;
  }
  .contact {
    position: absolute; right: 38px; top: 46px; text-align: right;
    font-family: "Carlito", sans-serif; font-size: 18px; line-height: 25px; color: var(--white);
  }
  .front-tagline {
    position: absolute; top: 394px; left: 0; width: 100%; text-align: center;
    font-family: "Open Sans", sans-serif; font-weight: 700; font-size: 16px;
    letter-spacing: 1.6px; color: var(--blue);
  }

  /* Back */
  .lockup {
    position: absolute; left: 70px; top: 255px; width: 310px; text-align: center;
    font-family: "Open Sans", sans-serif;
  }
  .lockup-name {
    display: flex; align-items: center; justify-content: center; gap: 10px;
    font-weight: 700; font-size: 27px; color: var(--ink); line-height: 1.1;
  }
  .lockup-name .dot { width: 18px; height: 18px; background: var(--blue); flex: none; }
  .lockup-tagline { font-size: 15.5px; letter-spacing: 1.4px; color: var(--ink-soft); margin-top: 3px; }
  .services { position: absolute; left: 426px; top: 122px; font-family: "Open Sans", sans-serif; }
  .services-heading { font-weight: 700; font-size: 26px; color: var(--blue); margin-bottom: 14px; }
  .services-list { list-style: none; }
  .services-list li {
    display: flex; align-items: center; gap: 7px;
    font-size: 17.5px; line-height: 26px; color: var(--ink-soft);
  }
  .services-list li::before {
    content: ""; width: 11px; height: 11px; background: var(--blue); flex: none;
  }
</style>
</head>
<body>
<div class="canvas">

  <section class="card card--front" aria-label="Business card front">
    <h1 class="front-title">NORRELL ADVISORY</h1>
    <div class="band">
      <div class="person">
        <div class="person-name">Megan Holloway</div>
        <div class="person-phone">0407913847</div>
      </div>
      <div class="brand-mark">
        <span class="dot"></span>
        <span class="brand-name">Norrell<br>Advisory</span>
      </div>
      <div class="contact">
        <div>norrelladvisorywa@mailbox-example.com</div>
        <div>www.norrelladvisorywa.example</div>
        <div>FB: norrelladvisorywa</div>
      </div>
    </div>
    <p class="front-tagline">STEADY STEPS * LASTING GAINS</p>
  </section>

  <section class="card card--back" aria-label="Business card back">
    <div class="lockup">
      <div class="lockup-name"><span class="dot"></span>NORRELL ADVISORY</div>
      <div class="lockup-tagline">STEADY STEPS LASTING GAINS</div>
    </div>
    <div class="services">
      <h2 class="services-heading">Providing assistance with</h2>
      <ul class="services-list">
        <li>Organisation &amp; Efficiency</li>
        <li>Revenue generation &amp; Marketing</li>
        <li>Financial Management</li>
        <li>Production quality &amp; delivery</li>
        <li>Systems &amp; Process documentation</li>
        <li>Exit Strategy</li>
      </ul>
    </div>
  </section>

</div>
</body>
</html>
```